Business Card Design Project

Looking to update our business cards. We have a logo with our slogan. We are an IT firm so we wouldlike a modern look.

Industry/Entity Type

Business

```html
<!DOCTYPE html>
<html lang="en">
<head>
<meta charset="utf-8">
<title>Norvale business card set</title>
<link rel="stylesheet" href="https://fonts.googleapis.com/css2?family=Open+Sans:wght@400;600;700&display=swap">
<style>
  :root {
    --stage: #ece8e3;
    --forest: #5f7f3c;
    --lime: #b0c242;
    --white: #ffffff;
    --ink: #3a3a3a;
    --ink-soft: #555555;
    --tagline: #2d2d2d;
    --label: #222222;
    --tech-deep: #0f2d72;
    --tech-mid: #2f6fd0;
    --tech-glow: #e6f1ff;
  }
  * { margin: 0; padding: 0; box-sizing: border-box; }
  html, body { width: 1200px; height: 788px; overflow: hidden; }
  body {
    background: var(--stage);
    font-family: "Open Sans", Arial, sans-serif;
    position: relative;
  }
  .view-label {
    position: absolute;
    width: 525px;
    text-align: center;
    font-size: 21px;
    color: var(--label);
  }
  .card {
    position: absolute;
    width: 525px;
    height: 300px;
    border-radius: 22px;
    overflow: hidden;
    background: var(--white);
    box-shadow: 0 3px 8px rgba(0,0,0,.25);
  }
  .card-front { left: 50px; top: 80px; height: 302px; }
  .card-back-white { left: 620px; top: 80px; }
  .card-back-lime { left: 50px; top: 455px; background: var(--lime); }
  .card-back-tech { left: 620px; top: 455px; }
  .front-shape { position: absolute; inset: 0; }
  .brand { position: absolute; text-align: center; }
  .brand-name { font-weight: 700; letter-spacing: 4px; line-height: 1; }
  .brand-tagline { font-weight: 700; line-height: 1; white-space: nowrap; }
  .brand-front { left: 28px; top: 56px; width: 230px; color: var(--white); }
  .brand-front .brand-name { font-size: 36px; letter-spacing: 5px; }
  .brand-front .brand-tagline { font-size: 10.5px; letter-spacing: 1.2px; margin-top: 9px; }
  .brand-center { left: 0; right: 0; top: 116px; color: var(--forest); }
  .brand-center .brand-name { font-size: 42px; letter-spacing: 6px; }
  .brand-center .brand-tagline { font-size: 13px; letter-spacing: 3.2px; color: var(--tagline); margin-top: 12px; }
  .brand-center .brand-name::before {
    content: "";
    display: inline-block;
    width: 12px; height: 12px;
    border-radius: 50%;
    background: currentColor;
    margin-right: 12px;
    vertical-align: middle;
  }
  .contact { position: absolute; right: 26px; text-align: right; color: var(--ink); white-space: nowrap; }
  .contact-name { top: 91px; font-size: 17px; font-weight: 700; }
  .contact-role { top: 113px; font-size: 12.5px; color: var(--ink-soft); }
  .contact-phone { top: 163px; font-size: 13.5px; }
  .contact-email { top: 193px; font-size: 13.5px; }
  .contact-web { top: 211px; font-size: 13.5px; }
  .contact-address { top: 258px; font-size: 13.5px; }
  .contact b { font-style: italic; }
  .tech-backdrop {
    position: absolute; inset: 0;
    background:
      radial-gradient(ellipse 220px 140px at 52% 52%, var(--tech-glow) 0%, rgba(170,200,255,.75) 40%, rgba(60,110,220,0) 85%),
      linear-gradient(100deg, var(--tech-deep) 0%, var(--tech-mid) 40%, #9aa9e4 68%, var(--tech-deep) 100%);
  }
</style>
</head>
<body>
  <div class="view-label" style="left:56px; top:34px;">Front</div>
  <div class="view-label" style="left:634px; top:34px;">Back - 1</div>
  <div class="view-label" style="left:56px; top:404px;">Back - 2</div>
  <div class="view-label" style="left:634px; top:404px;">Back - 3</div>

  <section class="card card-front">
    <svg class="front-shape" viewBox="0 0 525 302" width="525" height="302" aria-hidden="true">
      <path d="M0 0 H525 V8 C340 50 140 180 22 302 H0 Z" fill="var(--forest)"/>
      <path d="M525 22 C350 72 160 195 50 302 H34 C150 190 340 62 525 12 Z" fill="var(--lime)"/>
    </svg>
    <div class="brand brand-front">
      <div class="brand-name">NORVALE</div>
      <div class="brand-tagline">CLEAR TECHNOLOGY SUPPORT</div>
    </div>
    <div class="contact contact-name">Your Name</div>
    <div class="contact contact-role">Designation</div>
    <div class="contact contact-phone"><b>p</b> : +12 345 6789</div>
    <div class="contact contact-email"><b>e</b> : info@website.com</div>
    <div class="contact contact-web"><b>w</b> : www.website.com</div>
    <div class="contact contact-address">#0000, Street Name, Area Name, Country Code</div>
  </section>

  <section class="card card-back-white">
    <div class="brand brand-center">
      <div class="brand-name">NORVALE</div>
      <div class="brand-tagline">CLEAR TECHNOLOGY SUPPORT</div>
    </div>
  </section>

  <section class="card card-back-lime">
    <div class="brand brand-center">
      <div class="brand-name">NORVALE</div>
      <div class="brand-tagline">CLEAR TECHNOLOGY SUPPORT</div>
    </div>
  </section>

  <section class="card card-back-tech">
    <div class="tech-backdrop" role="img" aria-label="Abstract blue technology backdrop with a bright glowing swirl of light at the centre"></div>
    <div class="brand brand-center">
      <div class="brand-name">NORVALE</div>
      <div class="brand-tagline">CLEAR TECHNOLOGY SUPPORT</div>
    </div>
  </section>
</body>
</html>
```